Kestal-Materials. Limestone; improving the world

New Limestone company and need logo design.
Limestone offsets carbon mitigation industries restore and replenish soil fertilities in the Prairies, the breadbasket of the world. At the same time, Limestone is proving a critical emergent component of carbon capture sequestration technology will therefore play a critical role in the development of the western Canadian energy industries
Our limestone resources are situated in the foothills of the Canadian Rockies well-positioned above the sprawling fields of the vast peace district.
Agriculture and oli sites
Kestal Materials
3 page

```html
<!DOCTYPE html>
<html lang="en">
<head>
<meta charset="utf-8">
<title>Kestal Materials</title>
<link href="https://fonts.googleapis.com/css2?family=Open+Sans:wght@400;600;700&family=Lato:wght@400;700&display=swap" rel="stylesheet">
<style>
:root{
  --blue:#338dc6;
  --blue-dark:#2a7fb8;
  --ink:#1d1d1d;
  --text:#555;
  --header-bg:#f6f6f6;
  --services-bg:#e5e5e5;
  --help-bg:#ececec;
  --footer-bg:#426785;
  --footer-bar:#3d6079;
  --white:#fff;
}
*{margin:0;padding:0;box-sizing:border-box}
html,body{width:1200px;height:3062px;overflow:hidden}
body{position:relative;font-family:"Lato",sans-serif;color:var(--text);background:var(--white)}
.abs{position:absolute}
.center{left:0;width:1200px;text-align:center}
h1,h2,h3,h4{font-family:"Open Sans",sans-serif;font-weight:600}

/* header */
.site-header{top:0;left:0;width:1200px;height:107px;background:var(--header-bg)}
.brand{left:104px;top:8px;width:226px;display:flex;flex-direction:column;align-items:center;gap:8px}
.brand-mark{width:48px;height:48px;border-radius:50%;background:var(--blue)}
.brand-name{font-family:"Open Sans",sans-serif;font-weight:600;font-size:19px;color:var(--ink);letter-spacing:.4px;white-space:nowrap;line-height:22px}
.lang{left:993px;top:10px;width:95px;height:29px;background:var(--blue);color:var(--white);font-family:"Open Sans",sans-serif;font-size:11px;font-weight:700;display:flex;align-items:center;justify-content:center;gap:8px}
.nav a{position:absolute;top:60px;font-family:"Open Sans",sans-serif;font-size:14px;color:#444;text-decoration:none;white-space:nowrap}
.nav a.active{color:var(--blue)}
.nav a.active::after{content:"";position:absolute;left:0;right:0;bottom:-8px;height:2px;background:var(--blue)}

/* hero */
.hero{top:107px;left:0;width:1200px;height:553px;background:linear-gradient(180deg,#6d7466 0%,#8a8c84 35%,#7b8279 60%,#4e5a4a 100%)}
.hero-shade{top:107px;left:0;width:1200px;height:553px;background:rgba(0,0,0,.28)}
.hero-title{top:258px;font-size:64px;color:var(--white);letter-spacing:1px}
.hero-sub{top:336px;font-size:26px;color:var(--white);font-family:"Open Sans",sans-serif}
.btn-outline{border:2px solid var(--white);color:var(--white);font-family:"Open Sans",sans-serif;font-weight:600;font-size:16px;display:flex;align-items:center;justify-content:center}
.dots{top:609px;left:570px;display:flex;gap:9px}
.dots span{width:7px;height:7px;border-radius:50%;background:var(--white)}
.dots span.on{background:var(--blue)}

/* welcome */
.welcome{top:660px;left:0;width:1200px;height:451px;background:linear-gradient(180deg,#fbfcfa 0%,#f3f6f5 55%,#e4eef0 100%)}
.section-title{font-size:37px;color:var(--blue);letter-spacing:.5px}
.para{left:164px;width:872px;text-align:center;font-size:15.5px;line-height:26.5px;color:#555}
.btn-solid{background:var(--blue);color:var(--white);font-family:"Open Sans",sans-serif;font-weight:700;font-size:18px;display:flex;align-items:center;justify-content:center;letter-spacing:.3px}

/* services */
.services{top:1111px;left:0;width:1200px;height:678px;background:var(--services-bg)}
.card{top:1370px;width:308px;height:233px;border:2px solid var(--blue)}
.card-icon{position:absolute;top:-56px;left:96px;width:112px;height:112px;border-radius:50%;border:2px solid var(--blue);background:var(--services-bg);display:flex;align-items:center;justify-content:center}
.card h3{position:absolute;top:67px;left:0;width:100%;text-align:center;font-size:21px;color:#333;font-weight:400}
.card p{position:absolute;top:102px;left:22px;right:22px;text-align:center;font-size:14.5px;line-height:25px;color:#555}

/* about */
.about{top:1789px;left:0;width:1200px;height:402px;background:linear-gradient(180deg,#3b93cb 0%,#3a8dc4 50%,#3687bf 100%)}
.about-text{left:150px;width:900px;text-align:center;color:#eaf4fb;font-size:16.5px;line-height:23px}

/* help */
.help{top:2191px;left:0;width:1200px;height:501px;background:var(--help-bg)}
.field{border:1.5px solid #8fb7d6;background:#ececec;color:#666;font-size:16px;padding:10px 15px}

/* footer */
.footer{top:2692px;left:0;width:1200px;height:304px;background:var(--footer-bg)}
.footer-bar{top:2996px;left:0;width:1200px;height:66px;background:var(--footer-bar);border-top:1px solid #5a7d97}
.foot-h{top:2742px;font-size:23px;color:var(--white);font-weight:600}
.foot-list{top:2797px;list-style:none}
.foot-list li{font-size:12.5px;color:#e4edf3;height:31px}
.contact-line{display:flex;align-items:flex-start;gap:10px;color:#f0f5f8;font-size:12.5px;line-height:31px}
.contact-strong{font-size:15px;font-weight:700}
.social{top:2797px;left:903px;display:flex;gap:7px}
.social span{width:36px;height:36px;border-radius:50%;background:var(--white)}
.copyright{top:3020px;font-size:12.5px;color:#e4edf3}
</style>
</head>
<body>

<header class="abs site-header">
  <div class="abs brand"><span class="brand-mark"></span><span class="brand-name">KESTAL MATERIALS</span></div>
  <div class="abs lang">ENGLISH
    <svg width="8" height="6" viewBox="0 0 8 6"><path d="M1 1l3 3 3-3" stroke="#fff" stroke-width="1.4" fill="none"/></svg>
  </div>
  <nav class="nav">
    <a class="active" style="left:397px">HOME</a>
    <a style="left:488px">ABOUT US</a>
    <a style="left:605px">PRODUCTS</a>
    <a style="left:726px">SERVICES</a>
    <a style="left:835px">CAREERS</a>
    <a style="left:942px">CONTACT US</a>
    <svg class="abs" style="left:1075px;top:63px" width="13" height="13" viewBox="0 0 13 13"><circle cx="5.5" cy="5.5" r="4" stroke="#444" stroke-width="1.8" fill="none"/><path d="M8.5 8.5l3.5 3.5" stroke="#444" stroke-width="2"/></svg>
  </nav>
</header>

<section class="abs hero" role="img" aria-label="Aerial photograph of an open limestone quarry with terraced walls and a green pool, surrounded by farmland"></section>
<div class="abs hero-shade"></div>
<h1 class="abs center hero-title">KESTAL MATERIALS</h1>
<p class="abs center hero-sub">We are a New Limestone company</p>
<a class="abs btn-outline" style="left:530px;top:411px;width:140px;height:48px">LEARN MORE</a>
<div class="abs dots"><span class="on"></span><span></span><span></span><span></span></div>

<section class="abs welcome" role="img" aria-label="Faint misty limestone cliffs behind the welcome text"></section>
<h2 class="abs center section-title" style="top:732px">WELCOME TO KESTAL MATERIALS</h2>
<p class="abs para" style="top:788px">Lorem ipsum dolor sit amet, consectetur adipiscing elit, sed do eiusmod tempor incididunt ut labore et dolore magna aliqua. Ut enim ad minim veniam, quis nostrud exercitation ullamco laboris nisi ut aliquip ex ea commodo consequat. Duis aute irure dolor in reprehenderit in voluptate velit esse cillum dolore eu fugiat nulla pariatur.</p>
<p class="abs para" style="top:883px">Temporibus autem quibusdam et aut officiis debitis aut rerum necessitatibus saepe eveniet ut et voluptates repudiandae sint et molestiae non recusandae.</p>
<a class="abs btn-solid" style="left:461px;top:982px;width:278px;height:52px">READ MORE INFORMATION</a>

<section class="abs services"></section>
<h2 class="abs center section-title" style="top:1180px">NEW LIMESTONE SERVICES</h2>
<p class="abs" style="left:144px;width:912px;top:1235px;text-align:center;font-size:16.5px;line-height:25px;color:#555">lmestone offsets carbon mitigation industries restore and replenish soil fertility in the Prairies, the breadbasket of the world. At the same time, Limestone is proving a critical emergent component of carbon capture sequestration technology..</p>

<div class="abs card" style="left:112px">
  <div class="card-icon">
    <svg width="56" height="56" viewBox="0 0 56 56" fill="none" stroke="#338dc6" stroke-width="1.8">
      <circle cx="28" cy="36" r="16"/><ellipse cx="28" cy="36" rx="7" ry="16"/><path d="M12 36h32M14 28h28M14 44h28"/>
      <path d="M18 4c-2 3 2 5 0 8M26 2c-2 3 2 5 0 8M34 2c-2 3 2 5 0 8M42 4c-2 3 2 5 0 8"/>
    </svg>
  </div>
  <h3>Carbon Mitigation</h3>
  <p>Temporibus autem quibusdam et aut officiis debitis aut rerum necessitatibus saepe eveniet ut et voluptates.</p>
</div>
<div class="abs card" style="left:446px">
  <div class="card-icon">
    <svg width="56" height="56" viewBox="0 0 56 56" fill="none" stroke="#338dc6" stroke-width="1.8">
      <rect x="10" y="6" width="30" height="10"/><rect x="10" y="18" width="30" height="10"/><rect x="10" y="30" width="30" height="10"/><rect x="10" y="42" width="22" height="8"/>
      <path d="M42 52V38M37 43l5-5 5 5"/><path d="M14 11h12M14 23h12M14 35h12"/>
    </svg>
  </div>
  <h3>Restore and Replenish</h3>
  <p>Temporibus autem quibusdam et aut officiis debitis aut rerum necessitatibus saepe eveniet ut et voluptates.</p>
</div>
<div class="abs card" style="left:780px">
  <div class="card-icon">
    <svg width="60" height="56" viewBox="0 0 60 56" fill="none" stroke="#338dc6" stroke-width="1.8">
      <path d="M4 50h52L42 36H18z"/><path d="M30 38V14"/><path d="M30 24c-8 0-12-5-12-10 7 0 12 4 12 10zM30 18c0-7 5-11 12-11 0 6-5 11-12 11zM30 30c5-6 10-7 15-5-3 5-9 6-15 5z"/>
    </svg>
  </div>
  <h3>Soil Fertility</h3>
  <p>Temporibus autem quibusdam et aut officiis debitis aut rerum necessitatibus saepe eveniet ut et voluptates.</p>
</div>
<a class="abs btn-solid" style="left:522px;top:1664px;width:156px;height:52px">VIEW MORE</a>

<section class="abs about" role="img" aria-label="Blue-tinted landscape of rocky grassland and a country road under the about section"></section>
<h2 class="abs center section-title" style="top:1841px;color:#fff">ABOUT KESTAL MATERIALS</h2>
<p class="abs about-text" style="top:1897px">But I must explain to you how all this mistaken idea of denouncing pleasure and praising pain was born and I will give you a complete account of the system, and expound the actual teachings of the great explorer of the truth, the master-builder of human happiness. No one rejects, dislikes, or avoids pleasure itself, because it is pleasure</p>
<p class="abs about-text" style="top:1981px">At vero eos et accusamus et iusto odio dignissimos ducimus qui blanditiis praesentium voluptatum deleniti atque corrupti quos dolores et quas molestias excepturi sint occaecati cupiditate non provident</p>
<a class="abs btn-outline" style="left:530px;top:2063px;width:140px;height:48px">LEARN MORE</a>

<section class="abs help"></section>
<h2 class="abs center section-title" style="top:2245px">HOW CAN WE HELP YOU?</h2>
<p class="abs center" style="top:2301px;font-size:16px;color:#555">We respond to all feedback and inquiries and we look forward to hearing from you!</p>
<div class="abs field" style="left:112px;top:2368px;width:316px;height:43px">First Name</div>
<div class="abs field" style="left:442px;top:2368px;width:315px;height:43px">Last Name</div>
<div class="abs field" style="left:774px;top:2368px;width:315px;height:43px">Email Address</div>
<div class="abs field" style="left:112px;top:2427px;width:977px;height:92px">Message</div>
<a class="abs btn-solid" style="left:522px;top:2568px;width:156px;height:53px">SUBMIT NOW</a>

<footer class="abs footer"></footer>
<h4 class="abs foot-h" style="left:112px">Company</h4>
<ul class="abs foot-list" style="left:112px"><li>Home</li><li>About Us</li><li>Services</li><li>Latest News</li><li>Contact Us</li></ul>
<h4 class="abs foot-h" style="left:343px">Support</h4>
<ul class="abs foot-list" style="left:343px"><li>Terms of Use</li><li>Privacy Policy</li><li>Testimonials</li><li>Blog</li><li>Site Map</li></ul>
<h4 class="abs foot-h" style="left:557px">Contact Us</h4>
<div class="abs" style="left:557px;top:2792px">
  <div class="contact-line">
    <svg width="12" height="18" viewBox="0 0 12 18" style="margin-top:7px"><path d="M6 0a6 6 0 0 0-6 6c0 5 6 12 6 12s6-7 6-12a6 6 0 0 0-6-6z" fill="#fff"/><circle cx="6" cy="6" r="2.3" fill="#426785"/></svg>
    <div>Kestal Materials, Building Name,<br>N.'888, Norvale, Country Code.</div>
  </div>
  <div class="contact-line contact-strong" style="margin-top:11px">
    <svg width="15" height="15" viewBox="0 0 24 24" style="margin-top:8px"><path d="M6.6 10.8a15 15 0 0 0 6.6 6.6l2.2-2.2a1 1 0 0 1 1-.25 11 11 0 0 0 3.6.6 1 1 0 0 1 1 1V20a1 1 0 0 1-1 1A17 17 0 0 1 3 4a1 1 0 0 1 1-1h3.5a1 1 0 0 1 1 1c0 1.25.2 2.45.6 3.6a1 1 0 0 1-.25 1z" fill="#fff"/></svg>
    +000 555 0142
  </div>
  <div class="contact-line contact-strong" style="margin-top:14px">
    <svg width="16" height="12" viewBox="0 0 16 12" style="margin-top:11px"><rect width="16" height="12" rx="1" fill="#fff"/><path d="M1 1l7 6 7-6" stroke="#426785" stroke-width="1.4" fill="none"/></svg>
    info@kestalmaterials.example
  </div>
</div>
<h4 class="abs foot-h" style="left:903px">Connect With Us</h4>
<div class="abs social"><span></span><span></span><span></span><span></span></div>

<div class="abs footer-bar"></div>
<p class="abs center copyright">Copyrights © 2021 Kestal Materials. All rights reserved.</p>

</body>
</html>
```